Harborlight Amusement Collective (HAC)

We need a business card design for Harborlight Amusement Collective. Modern and sleek looking, with all critical information. Open to single or double sided designs, if double sided info needs to be all on one side. The main Logo is Harborlight Amusement collective and must be on the card. The other three logos are for the brands that fall under the group, they might be good on the back.

Industry/Entity Type

Business

```html
<!DOCTYPE html>
<html lang="en">
<head>
<meta charset="utf-8">
<title>Harborlight Amusement Collective — Business Card</title>
<link rel="stylesheet" href="https://fonts.googleapis.com/css2?family=Montserrat:wght@400;500;600&family=Saira+Semi+Condensed:wght@600&display=swap">
<style>
  :root {
    --page-bg: #e9e6e1;
    --card-blue: #24538e;
    --card-blue-deep: #1d477d;
    --wordmark: #d9ccae;
    --name: #e3d8bf;
    --muted-gold: #c9b78f;
    --contact: #e6dfcf;
    --mark: #eee9dd;
  }
  * { box-sizing: border-box; margin: 0; padding: 0; }
  html, body { width: 1200px; height: 1054px; overflow: hidden; }
  body {
    background: var(--page-bg);
    font-family: "Montserrat", Arial, sans-serif;
    position: relative;
  }
  .business-card {
    position: absolute;
    left: 100px;
    top: 224px;
    width: 1000px;
    height: 605px;
    background: linear-gradient(100deg, var(--card-blue-deep) 0%, var(--card-blue) 55%, var(--card-blue-deep) 100%);
    box-shadow: 0 10px 30px rgba(0,0,0,0.18);
  }
  .brand-mark {
    position: absolute;
    left: 40px;
    top: 40px;
    width: 450px;
    height: 520px;
    display: flex;
    align-items: center;
    justify-content: center;
    gap: 28px;
  }
  .brand-mark__square {
    width: 70px;
    height: 70px;
    background: var(--mark);
  }
  .brand-mark__name {
    font-weight: 600;
    font-size: 128px;
    letter-spacing: 4px;
    color: var(--mark);
    line-height: 1;
  }
  .company-name {
    position: absolute;
    right: 55px;
    top: 50px;
    text-align: right;
    font-weight: 600;
    color: var(--wordmark);
    font-size: 26px;
    letter-spacing: 1px;
    line-height: 1.45;
    text-transform: uppercase;
  }
  .company-name__line2 { letter-spacing: 7px; }
  .contact-block {
    position: absolute;
    right: 55px;
    top: 238px;
    text-align: right;
  }
  .person-name {
    font-family: "Saira Semi Condensed", "Arial Narrow", sans-serif;
    font-weight: 600;
    font-size: 44px;
    color: var(--name);
    line-height: 1.1;
  }
  .person-role {
    font-size: 23px;
    color: var(--contact);
    margin-top: 6px;
  }
  .address {
    font-size: 23px;
    color: var(--muted-gold);
    line-height: 1.45;
    margin-top: 46px;
    font-style: normal;
  }
  .contact-list {
    list-style: none;
    margin-top: 18px;
  }
  .contact-list li {
    font-size: 22px;
    color: var(--contact);
    line-height: 35px;
    display: flex;
    justify-content: flex-end;
    align-items: center;
    gap: 12px;
  }
  .contact-icon { width: 20px; height: 20px; fill: var(--contact); }
</style>
</head>
<body>
  <section class="business-card" aria-label="Harborlight Amusement Collective business card">
    <div class="brand-mark">
      <div class="brand-mark__square" aria-hidden="true"></div>
      <div class="brand-mark__name">HAC</div>
    </div>

    <h1 class="company-name">
      <span>Harborlight Amusement</span><br>
      <span class="company-name__line2">Collective</span>
    </h1>

    <div class="contact-block">
      <p class="person-name">Marlow Keane</p>
      <p class="person-role">Managing Director</p>
      <address class="address">48 Quayside Row, Port<br>Linden, US 204518</address>
      <ul class="contact-list">
        <li>555.284.0917
          <svg class="contact-icon" viewBox="0 0 20 20" aria-hidden="true"><path d="M2 6c0-2 3-3 8-3s8 1 8 3v2h-4V6.5c-1-.6-7-.6-8 0V8H2z"/><path d="M5 9h10l2 8H3z"/><circle cx="10" cy="13" r="2" fill="#24538e"/></svg>
        </li>
        <li>mkeane@harborlightac.com
          <svg class="contact-icon" viewBox="0 0 20 20" aria-hidden="true"><rect x="1" y="4" width="18" height="12"/><path d="M1 4l9 7 9-7" fill="none" stroke="#24538e" stroke-width="1.6"/></svg>
        </li>
        <li>www.harborlightac.com
          <svg class="contact-icon" viewBox="0 0 20 20" aria-hidden="true"><circle cx="10" cy="10" r="8.5"/><g fill="none" stroke="#24538e" stroke-width="1.2"><ellipse cx="10" cy="10" rx="3.5" ry="8.5"/><path d="M1.5 10h17M3 6h14M3 14h14"/></g></svg>
        </li>
      </ul>
    </div>
  </section>
</body>
</html>
```